Brookvale Estates LLC stationary for a real estate property management company.

Create stationary (letterhead, envelopes, business cards) using Brookvale Estates LLC logo as primary creative element. Stationary design needs to be horizontal, leaving as much space as possible for correspondence copy. See attached Creative Brief and past stationary files for details.

Target Market(s)

Prospective apartment residents and current residents, vendors, and government agencies.

Industry/Entity Type

Property Management

Contact Information for Business Card

Business card employee title: Property Manager. Should include address, phone, fax, email, website, slogan, and Brookvale Estates logo.

Font styles to use
Sans Serif

Colors
0592cd
000000

Requirements
Must have
• Tone should be conservative, institutional, business (i.e. banking, finance, real estate). Must include: address, phone, fax, website, and slogan (see attached Creative Brief). Should be a horizontal design, leaving as much room as possible for letter correspondence copy.
Nice to have
• Please use an Arial or Helvetica style font.
Should not have
• Letterhead layout should leave as much room as possible for copy.

```html
<!DOCTYPE html>
<html lang="en">
<head>
<meta charset="utf-8">
<title>Brookvale Estates LLC — Stationery</title>
<link href="https://fonts.googleapis.com/css2?family=Arimo:wght@400;700&family=Michroma&display=swap" rel="stylesheet">
<style>
  :root{
    --blue:#1c74b4;
    --dark:#333335;
    --ink:#3a3a3a;
    --paper:#ffffff;
    --bg:#e8e8e8;
  }
  *{box-sizing:border-box;margin:0;padding:0}
  html,body{width:1200px;height:938px;overflow:hidden}
  body{background:var(--bg);font-family:"Arimo",Arial,sans-serif;color:var(--ink);position:relative}
  .piece{position:absolute;background:var(--paper);overflow:hidden}
  .band{position:absolute;left:0;top:0;bottom:0;background:var(--dark)}
  .accent{position:absolute;background:var(--blue)}

  /* brand name block */
  .brand{position:absolute;display:flex;align-items:center;color:var(--blue);font-weight:700}
  .brand .square{background:var(--blue);flex:none}
  .brand .words{display:flex;flex-direction:column;line-height:1;text-transform:uppercase}

  /* letterhead */
  .letterhead{left:184px;top:67px;width:388px;height:546px}
  .letterhead .band{width:30px}
  .letterhead .accent{left:22px;top:25px;width:9px;height:78px}
  .letterhead .brand{left:46px;top:36px;gap:6px}
  .letterhead .brand .square{width:20px;height:20px}
  .letterhead .brand .words span:first-child{font-size:15px;letter-spacing:.2px}
  .letterhead .brand .words span:last-child{font-size:7px;letter-spacing:1.2px;margin-top:2px}
  .letter{position:absolute;left:38px;top:138px;width:300px;font-size:5.2px;line-height:1.55;color:#555}
  .letter p{margin-bottom:6px}
  .letter .gap{margin-bottom:20px}
  .letter strong{color:#333}
  .signature{width:38px;height:22px;background:linear-gradient(90deg,#f3f3f3,#e4e4e4);margin:4px 0 8px}
  .contacts{position:absolute;left:13px;top:448px;list-style:none}
  .contacts li{display:flex;align-items:center;height:17px;font-size:5.3px;color:#444;line-height:1.25}
  .ico{width:19px;height:12px;background:var(--blue);border-radius:1px;display:flex;align-items:center;justify-content:center;margin-right:5px;flex:none}
  .ico svg{width:7px;height:7px;fill:none;stroke:#fff;stroke-width:1.6}
  .letterhead .slogan{position:absolute;right:22px;bottom:14px;font-size:6px;font-style:normal;color:var(--blue);font-weight:700;letter-spacing:.4px}

  /* folder */
  .folder{left:637px;top:41px;width:458px;height:575px}
  .folder .band{width:56px}
  .folder .accent{left:47px;top:220px;width:9px;height:135px}
  .folder .brand{left:102px;top:250px;gap:12px}
  .folder .brand .square{width:60px;height:60px}
  .folder .brand .words span:first-child{font-size:42px;letter-spacing:.5px}
  .folder .brand .words span:last-child{font-size:16px;letter-spacing:3.4px;margin-top:6px}
  .web{position:absolute;display:flex;align-items:center;font-family:"Michroma","Arimo",sans-serif;color:var(--dark)}
  .folder .web{left:24px;top:510px;font-size:12px;letter-spacing:5px}
  .folder .web .ico{width:35px;height:24px;margin-right:14px}
  .folder .web .ico svg{width:13px;height:13px}

  /* business cards */
  .card{width:176px;height:99px;border-radius:7px}
  .card .foot{position:absolute;left:0;right:0;bottom:0;height:22px;background:#1f1f20}
  .card .accent{left:28px;bottom:21px;width:35px;height:3px}
  .card-front{left:46px;top:659px}
  .card-back{left:46px;top:785px}
  .card-back .foot{background:linear-gradient(90deg,#444,#2a2a2a)}
  .vert{position:absolute;writing-mode:vertical-rl;transform:rotate(180deg);white-space:nowrap}
  .card .brand.vert{display:flex;flex-direction:row;align-items:center;gap:3px}
  .card .brand .square{width:8px;height:8px}
  .card .brand .words span:first-child{font-size:8px}
  .card .brand .words span:last-child{font-size:3.6px;letter-spacing:.6px;margin-top:1px}
  .card-front .brand{left:70px;top:8px;height:66px}
  .person{left:96px;top:8px;height:66px;font-size:6px;line-height:1.3;color:#333}
  .person span{display:block;font-size:4.8px;color:#666}
  .card-lines{left:120px;top:8px;height:66px;font-size:3.8px;line-height:2.2;color:#444}
  .card-lines span{display:block}
  .card .chip{position:absolute;bottom:6px;width:10px;height:11px;background:var(--blue);border-radius:1px;display:flex;align-items:center;justify-content:center}
  .card .chip svg{width:5px;height:5px;fill:none;stroke:#fff;stroke-width:1.8}
  .card-back .brand{left:86px;top:8px;height:66px}
  .card-back .slogan{left:104px;top:8px;height:66px;font-size:4.2px;color:#555}

  /* envelope front */
  .envelope{left:266px;top:674px;width:432px;height:208px}
  .envelope .band{width:30px}
  .envelope .accent{left:26px;top:22px;width:4px;height:62px}
  .envelope .brand{left:42px;top:37px;gap:6px}
  .envelope .brand .square{width:20px;height:20px}
  .envelope .brand .words span:first-child{font-size:15px}
  .envelope .brand .words span:last-child{font-size:7px;letter-spacing:1.2px;margin-top:2px}
  .envelope .web{left:10px;top:181px;font-size:7.5px;letter-spacing:3px}
  .envelope .web .ico{width:18px;height:13px;margin-right:11px}

  /* envelope back */
  .envelope-back{left:736px;top:672px;width:434px;height:208px}
  .flap{position:absolute;left:0;top:0;right:0;height:72px;background:var(--dark);border-radius:0 0 40px 40px;display:flex;align-items:center;justify-content:center}
  .flap .web{position:static;color:#fff;font-size:11px;letter-spacing:5px;margin-top:-2px}
</style>
</head>
<body>

<section class="piece letterhead" aria-label="Letterhead">
  <div class="band"></div>
  <div class="accent"></div>
  <div class="brand">
    <span class="square"></span>
    <span class="words"><span>Brookvale</span><span>Estates LLC</span></span>
  </div>
  <div class="letter">
    <p>July 2, 2012</p>
    <p><strong>Dear CH,</strong><br>ABC Building, def St., Country Name</p>
    <p class="gap">Thank you for choosing Brookvale Estates for your residence. This letter confirms the details of your lease renewal and outlines the services our team provides throughout the year. Our office is available for maintenance requests, payment questions and general support during regular business hours. Please review the enclosed documents carefully, sign where indicated and return them at your earliest convenience so that we can complete the process without delay.</p>
    <p class="gap">We value every resident and vendor we work with, and we remain committed to clear communication, fair practices and well maintained homes for the community.</p>
    <p>Thank you for choosing Brookvale Estates for your residence. This letter confirms the details of your lease renewal and outlines the services our team provides throughout the year. Our office is available for maintenance requests, payment questions and general support during regular business hours. Please review the enclosed documents carefully, sign where indicated and return them at your earliest convenience so that we can complete the process without delay.</p>
    <p>Best Regards,</p>
    <div class="signature" role="img" aria-label="Handwritten signature"></div>
    <p><strong>Aaron Pell</strong><br>Director</p>
    <p>ABC Building, def St., Country Name</p>
  </div>
  <ul class="contacts">
    <li><span class="ico"><svg viewBox="0 0 10 10"><path d="M2 1.5l2 2-1 1.2a6 6 0 0 0 2.3 2.3L6.5 6l2 2-1.2 1.2C4.5 9 1 5.5.8 2.7z"/></svg></span>Phone 555-014-2270</li>
    <li><span class="ico"><svg viewBox="0 0 10 10"><rect x="2" y="1" width="6" height="3"/><rect x="1" y="4" width="8" height="4"/><path d="M3 8v1.5h4V8"/></svg></span>Fax 555-014-2271</li>
    <li><span class="ico"><svg viewBox="0 0 10 10"><rect x="1" y="2.5" width="8" height="5.5"/><path d="M1 2.5l4 3 4-3"/></svg></span>dwhitfield@brookvalehomes.com</li>
    <li><span class="ico"><svg viewBox="0 0 10 10"><circle cx="5" cy="5" r="4"/><path d="M1 5h8M5 1c-2 2.5-2 5.5 0 8M5 1c2 2.5 2 5.5 0 8"/></svg></span>www.brookvalehomes.com</li>
    <li><span class="ico"><svg viewBox="0 0 10 10"><path d="M1 5.2L5 1.5l4 3.7M2.5 4v4.5h5V4"/></svg></span><span>4120 Alder Creek Road<br>Fairhaven, OH 45011</span></li>
  </ul>
  <p class="slogan">Homes managed with care</p>
</section>

<section class="piece folder" aria-label="Presentation folder">
  <div class="band"></div>
  <div class="accent"></div>
  <div class="brand">
    <span class="square"></span>
    <span class="words"><span>Brookvale</span><span>Estates LLC</span></span>
  </div>
  <div class="web">
    <span class="ico"><svg viewBox="0 0 10 10"><circle cx="5" cy="5" r="4"/><path d="M1 5h8M5 1c-2 2.5-2 5.5 0 8M5 1c2 2.5 2 5.5 0 8"/></svg></span>
    www.brookvalehomes.com
  </div>
</section>

<section class="piece card card-front" aria-label="Business card front">
  <div class="foot"></div>
  <div class="accent"></div>
  <div class="brand vert">
    <span class="square"></span>
    <span class="words"><span>Brookvale</span><span>Estates LLC</span></span>
  </div>
  <div class="vert person">Dana Whitfield<span>Property Manager</span></div>
  <div class="vert card-lines">
    <span>P 555-014-2270</span>
    <span>F 555-014-2271</span>
    <span>dwhitfield@brookvalehomes.com</span>
    <span>www.brookvalehomes.com</span>
    <span>4120 Alder Creek Road</span>
    <span>Fairhaven, OH 45011</span>
  </div>
  <span class="chip" style="left:98px"><svg viewBox="0 0 10 10"><circle cx="5" cy="3.5" r="2"/><path d="M1.5 9.5a3.5 3.5 0 0 1 7 0"/></svg></span>
  <span class="chip" style="left:122px"><svg viewBox="0 0 10 10"><path d="M2 1.5l2 2-1 1.2a6 6 0 0 0 2.3 2.3L6.5 6l2 2-1.2 1.2C4.5 9 1 5.5.8 2.7z"/></svg></span>
  <span class="chip" style="left:135px"><svg viewBox="0 0 10 10"><rect x="1" y="2.5" width="8" height="5.5"/><path d="M1 2.5l4 3 4-3"/></svg></span>
  <span class="chip" style="left:148px"><svg viewBox="0 0 10 10"><circle cx="5" cy="5" r="4"/><path d="M1 5h8"/></svg></span>
  <span class="chip" style="left:161px"><svg viewBox="0 0 10 10"><path d="M1 5.2L5 1.5l4 3.7M2.5 4v4.5h5V4"/></svg></span>
</section>

<section class="piece card card-back" aria-label="Business card back">
  <div class="foot"></div>
  <div class="accent"></div>
  <div class="brand vert">
    <span class="square"></span>
    <span class="words"><span>Brookvale</span><span>Estates LLC</span></span>
  </div>
  <p class="vert slogan">Homes managed with care</p>
  <span class="chip" style="left:138px"></span>
  <span class="chip" style="left:155px"></span>
</section>

<section class="piece envelope" aria-label="Envelope front">
  <div class="band"></div>
  <div class="accent"></div>
  <div class="brand">
    <span class="square"></span>
    <span class="words"><span>Brookvale</span><span>Estates LLC</span></span>
  </div>
  <div class="web">
    <span class="ico"><svg viewBox="0 0 10 10"><circle cx="5" cy="5" r="4"/><path d="M1 5h8M5 1c-2 2.5-2 5.5 0 8M5 1c2 2.5 2 5.5 0 8"/></svg></span>
    www.brookvalehomes.com
  </div>
</section>

<section class="piece envelope-back" aria-label="Envelope back">
  <div class="flap"><span class="web">www.brookvalehomes.com</span></div>
</section>

</body>
</html>
```